New Business Card Design Project

We would like a business card that represents the sale of boat, home, auto, and life insurance.

The logo can change colors to meet the look of the design if needed.

Industry/Entity Type

Business

```html
<!DOCTYPE html>
<html lang="en">
<head>
<meta charset="utf-8">
<title>Meridale Financial – Business Card</title>
<link rel="stylesheet" href="https://fonts.googleapis.com/css2?family=Lato:wght@400;700;900&display=swap">
<style>
  :root {
    --stage: #2b2b2d;
    --teal: #3f6f86;
    --teal-deep: #2f5a70;
    --teal-light: #4a7f98;
    --ink: #3a3b3d;
    --paper: #f7f7f6;
    --white: #ffffff;
  }
  * { box-sizing: border-box; margin: 0; padding: 0; }
  html, body {
    width: 1200px; height: 997px; overflow: hidden;
    background: var(--stage);
    font-family: "Lato", sans-serif;
  }
  .stage { position: relative; width: 1200px; height: 997px; }

  .card {
    position: absolute;
    width: 540px; height: 309px;
    border-radius: 22px;
    overflow: hidden;
    box-shadow: 0 18px 40px rgba(0,0,0,.45);
  }

  /* Back side */
  .card-back {
    left: 60px; top: 150px;
    background: linear-gradient(160deg, var(--teal-light), var(--teal-deep));
    display: flex; flex-direction: column; align-items: center; justify-content: center;
  }
  .card-back .brand-name {
    font-size: 46px; font-weight: 400; letter-spacing: 6px;
    color: var(--ink);
    margin-top: -20px;
  }
  .services {
    position: absolute; bottom: 34px; left: 0; right: 0;
    display: flex; justify-content: center; align-items: center; gap: 18px;
    font-size: 13px; letter-spacing: 3px; color: var(--ink);
  }
  .services .divider { width: 2px; height: 22px; background: rgba(255,255,255,.75); }

  /* Front side */
  .card-front {
    left: 600px; top: 560px;
    background: var(--paper);
  }
  .front-brand {
    position: absolute; left: 0; top: 0; width: 300px; height: 100%;
    display: flex; align-items: center; justify-content: center;
  }
  .front-brand .brand-name {
    font-size: 36px; font-weight: 400; letter-spacing: 5px; color: var(--ink);
  }
  .stripe { position: absolute; top: 0; height: 100%; background: var(--teal); }
  .stripe-a { left: 304px; width: 4px; }
  .stripe-b { left: 314px; width: 4px; }
  .info-panel {
    position: absolute; left: 326px; top: 0; right: 0; height: 100%;
    background: linear-gradient(160deg, var(--teal-light), var(--teal-deep));
    color: var(--white);
    padding: 34px 18px 0 22px;
  }
  .person-name { font-size: 19px; font-weight: 900; }
  .person-role { font-size: 12px; font-weight: 700; letter-spacing: .5px; margin-top: 2px; }
  .contact-list { list-style: none; margin-top: 62px; }
  .contact-list li {
    display: flex; align-items: center; gap: 8px;
    font-size: 12px; margin-bottom: 7px; white-space: nowrap;
  }
  .contact-list svg { width: 12px; height: 12px; flex: none; fill: none; stroke: var(--white); stroke-width: 1.6; }
</style>
</head>
<body>
<main class="stage">

  <section class="card card-back" aria-label="Card back">
    <div class="brand-name">MERIDALE</div>
    <div class="services">
      <span>BOAT</span><span class="divider"></span>
      <span>HOME</span><span class="divider"></span>
      <span>AUTO</span><span class="divider"></span>
      <span>LIFE INSURANCE</span>
    </div>
  </section>

  <section class="card card-front" aria-label="Card front">
    <div class="front-brand">
      <div class="brand-name">MERIDALE</div>
    </div>
    <span class="stripe stripe-a"></span>
    <span class="stripe stripe-b"></span>
    <div class="info-panel">
      <div class="person-name">Dana Whitlow</div>
      <div class="person-role">FOUNDER/CEO</div>
      <ul class="contact-list">
        <li>
          <svg viewBox="0 0 12 12"><path d="M2 3c0-1 1-1.5 4-1.5S10 2 10 3v1H8V3H4v1H2z M3 5h6l1 5H2z"/></svg>
          555 014 7950
        </li>
        <li>
          <svg viewBox="0 0 12 12"><rect x="3" y="1" width="6" height="4"/><rect x="1.5" y="5" width="9" height="6"/></svg>
          555 014 7000
        </li>
        <li>
          <svg viewBox="0 0 12 12"><rect x="1" y="2.5" width="10" height="7"/><path d="M1 2.5l5 4 5-4"/></svg>
          dana@harborlineco.com
        </li>
        <li>
          <svg viewBox="0 0 12 12"><path d="M5 7l2-2 M4 5.5L2.5 7a1.8 1.8 0 0 0 2.5 2.5L6.5 8 M8 6.5L9.5 5A1.8 1.8 0 0 0 7 2.5L5.5 4"/></svg>
          www.harborlineco.com
        </li>
      </ul>
    </div>
  </section>

</main>
</body>
</html>
```